Property development business card design

New build residential property developers. I want a professional look but customer friendly so not too corporate. I'm not sure what logo will look best so open to designs with either. Thank you

Also i don't want both names on one card its 2 names for 2 different cards but with the same design.

Industry/Entity Type

Residential

Contact Information for Business Card

KTR Developments Ltd,
58 Fennel Lane,
Ipswich,
Suffolk,
IP7 4WD

Property Research Manager
Morven Tadlock

Managing Director
Dilan Perriwick

```html
<!DOCTYPE html>
<html lang="en">
<head>
<meta charset="utf-8">
<title>KTR Developments – Business Card</title>
<link rel="stylesheet" href="https://fonts.googleapis.com/css2?family=Questrial&display=swap">
<style>
  :root {
    --page-bg: #e9ebee;
    --card-bg: #ffffff;
    --ink: #2a2a2a;
    --ink-soft: #3a3a3a;
    --brand-grey: #8a8d91;
    --name-blue: #2d3a8c;
    --blue-deep: #2b46a8;
    --blue-bright: #1aa8e8;
    --swoosh-dark: #3b3d40;
    --swoosh-light: #c4c7cb;
    --mark-blue: #1f86d0;
  }
  * { box-sizing: border-box; margin: 0; padding: 0; }
  html, body {
    width: 1200px; height: 800px; overflow: hidden;
    background: var(--page-bg);
    font-family: "Questrial", "Century Gothic", sans-serif;
  }
  .card {
    position: absolute; left: 75px; top: 100px;
    width: 1050px; height: 600px;
    background: var(--card-bg);
    box-shadow: 0 6px 24px rgba(0,0,0,0.12);
    overflow: hidden;
  }
  .card__wave { position: absolute; inset: 0; width: 100%; height: 100%; }

  .contact {
    position: absolute; left: 72px; top: 110px;
    color: var(--ink); font-size: 21px; line-height: 1.45;
  }
  .contact__address { margin-bottom: 34px; }
  .contact__list { list-style: none; }
  .contact__item {
    display: flex; align-items: center; gap: 12px;
    font-size: 18px; height: 36px;
  }
  .contact__icon { width: 18px; height: 18px; flex: none; }

  .brand {
    position: absolute; left: 440px; top: 82px;
    display: flex; align-items: center; gap: 26px;
  }
  .brand__dot {
    width: 150px; height: 150px; border-radius: 50%;
    background: var(--mark-blue);
  }
  .brand__name {
    font-size: 38px; letter-spacing: 2px;
    color: var(--brand-grey); text-transform: uppercase;
  }

  .person {
    position: absolute; right: 70px; top: 250px;
    text-align: right;
  }
  .person__name {
    font-size: 30px; letter-spacing: 2px;
    color: var(--name-blue); text-transform: uppercase;
  }
  .person__role { font-size: 22px; color: var(--ink-soft); margin-top: 4px; }
</style>
</head>
<body>
  <main class="card">
    <svg class="card__wave" viewBox="0 0 1050 600" preserveAspectRatio="none" aria-hidden="true">
      <defs>
        <linearGradient id="waveBlue" x1="0" y1="0" x2="1" y2="0">
          <stop offset="0" stop-color="var(--blue-deep)"/>
          <stop offset="1" stop-color="var(--blue-bright)"/>
        </linearGradient>
        <linearGradient id="waveSteel" x1="0" y1="0" x2="1" y2="0">
          <stop offset="0" stop-color="var(--swoosh-dark)"/>
          <stop offset="0.4" stop-color="var(--swoosh-light)"/>
          <stop offset="0.75" stop-color="var(--swoosh-light)"/>
          <stop offset="1" stop-color="var(--swoosh-dark)"/>
        </linearGradient>
      </defs>
      <path fill="url(#waveSteel)"
        d="M0,418 C200,486 380,500 560,450 C760,396 900,358 1050,358
           L1050,378 C900,378 760,412 560,466 C380,514 200,500 0,432 Z"/>
      <path fill="url(#waveBlue)"
        d="M0,446 C200,510 380,528 560,478 C760,422 900,390 1050,392 L1050,600 L0,600 Z"/>
    </svg>

    <section class="contact">
      <p class="contact__address">58 Fennel Lane<br>Ipswich IP7 4WD</p>
      <ul class="contact__list">
        <li class="contact__item">
          <svg class="contact__icon" viewBox="0 0 24 24"><path fill="var(--ink)" d="M6.6 10.8a15 15 0 0 0 6.6 6.6l2.2-2.2a1 1 0 0 1 1-.25 11.4 11.4 0 0 0 3.6.57 1 1 0 0 1 1 1V20a1 1 0 0 1-1 1A17 17 0 0 1 3 4a1 1 0 0 1 1-1h3.5a1 1 0 0 1 1 1c0 1.25.2 2.45.57 3.6a1 1 0 0 1-.25 1z"/></svg>
          <span>01473 555 018</span>
        </li>
        <li class="contact__item">
          <svg class="contact__icon" viewBox="0 0 24 24"><rect x="6" y="2" width="12" height="20" rx="2" fill="none" stroke="var(--ink)" stroke-width="2"/><circle cx="12" cy="18" r="1.3" fill="var(--ink)"/></svg>
          <span>07700 555 264</span>
        </li>
        <li class="contact__item">
          <svg class="contact__icon" viewBox="0 0 24 24"><rect x="3" y="9" width="18" height="12" rx="1.5" fill="var(--ink)"/><rect x="7" y="3" width="10" height="7" fill="none" stroke="var(--ink)" stroke-width="2"/><rect x="6" y="13" width="12" height="2" fill="#fff"/></svg>
          <span>01473 555 019</span>
        </li>
        <li class="contact__item">
          <svg class="contact__icon" viewBox="0 0 24 24"><rect x="2" y="5" width="20" height="14" rx="1.5" fill="var(--ink)"/><path d="M3 6l9 7 9-7" fill="none" stroke="#fff" stroke-width="1.6"/></svg>
          <span>hello@ktrdevelopments.co.uk</span>
        </li>
        <li class="contact__item">
          <svg class="contact__icon" viewBox="0 0 24 24"><g fill="none" stroke="var(--ink)" stroke-width="1.8"><circle cx="12" cy="12" r="9.5"/><ellipse cx="12" cy="12" rx="4" ry="9.5"/><path d="M2.5 12h19M4 7h16M4 17h16"/></g></svg>
          <span>www.ktrdevelopments.co.uk</span>
        </li>
      </ul>
    </section>

    <header class="brand">
      <span class="brand__dot" aria-hidden="true"></span>
      <h1 class="brand__name">KTR Developments</h1>
    </header>

    <section class="person">
      <h2 class="person__name">Dilan Perriwick</h2>
      <p class="person__role">Managing Director</p>
    </section>
  </main>
</body>
</html>
```